Business Card Design

We are a florist shop that also stocks a range of giftware and jewellery. I would like a new design that incorporates a light green background. If you could use a skeleton leaf somewhere in the design that would be great. I would also like to incorporate the find us on Linkverse logo on this design.

Florist

Contact Information for Business Card

Petals on Harwood
42 Harwood street
Kellbrook Downs 3917
Phone: 0351938264
Fax : 0351938207
email: poh@wattlemail.net.au

Proprietors : Dana & Lee Morcombe

```html
<!DOCTYPE html>
<html lang="en">
<head>
<meta charset="utf-8">
<title>Petals on Harwood – Business Card</title>
<link rel="stylesheet" href="https://fonts.googleapis.com/css2?family=Dancing+Script:wght@400&family=Source+Sans+3:wght@400&display=swap">
<style>
  :root {
    --backdrop: #4a4a4a;
    --card-top: #c8e2a4;
    --card-mid: #eef6e2;
    --card-white: #ffffff;
    --title-red: #c1272d;
    --name-ink: #111111;
    --rule-green: #006b3a;
    --band-top: #80c343;
    --band-bottom: #55b848;
    --band-ink: #ffffff;
    --decor-mint: #cfe8d8;
    --decor-pale: #e4f1dc;
  }
  * { margin: 0; padding: 0; box-sizing: border-box; }
  html, body { width: 1200px; height: 999px; overflow: hidden; background: var(--backdrop); }
  .card {
    position: absolute; left: 68px; top: 192px; width: 1064px; height: 614px;
    background: linear-gradient(to bottom, var(--card-top) 0%, var(--card-mid) 35%, var(--card-white) 68%);
    overflow: hidden;
    font-family: "Source Sans 3", "Myriad Pro", sans-serif;
  }
  .decor { position: absolute; }
  .decor--flower-large {
    left: 770px; top: 180px; width: 294px; height: 233px;
    background: radial-gradient(ellipse at 55% 70%, var(--decor-mint) 0%, var(--decor-pale) 55%, rgba(228,241,220,0) 75%);
  }
  .decor--flower-mid {
    left: 665px; top: 345px; width: 150px; height: 68px;
    background: radial-gradient(ellipse at 50% 80%, var(--decor-mint) 0%, rgba(228,241,220,0) 70%);
  }
  .decor--flower-small {
    left: 30px; top: 340px; width: 140px; height: 73px;
    background: radial-gradient(ellipse at 50% 80%, var(--decor-mint) 0%, rgba(228,241,220,0) 70%);
  }
  .decor--butterfly {
    left: 168px; top: 312px; width: 104px; height: 88px;
    background: radial-gradient(ellipse at 40% 45%, var(--decor-pale) 0%, rgba(228,241,220,0) 70%);
  }
  .brand-title {
    position: absolute; left: 0; right: 0; top: 66px;
    text-align: center;
    font-family: "Dancing Script", cursive;
    font-weight: 400;
    font-size: 118px; line-height: 1;
    color: var(--title-red);
  }
  .proprietors {
    position: absolute; left: 0; right: 0; top: 272px;
    text-align: center;
    font-size: 47px; line-height: 1;
    color: var(--name-ink);
  }
  .rule { position: absolute; left: 0; top: 413px; width: 100%; height: 13px; background: var(--rule-green); }
  .contact-band {
    position: absolute; left: 0; top: 426px; width: 100%; height: 188px;
    background: linear-gradient(to bottom, var(--band-top), var(--band-bottom));
    color: var(--band-ink);
    font-size: 29px; line-height: 37.5px;
  }
  .address { position: absolute; left: 44px; top: 42px; font-style: normal; }
  .contact-list { position: absolute; left: 704px; top: 42px; list-style: none; }
  .contact-list li { display: flex; align-items: center; height: 37.5px; }
  .contact-list svg { width: 28px; height: 28px; margin-right: 38px; fill: var(--band-ink); }
</style>
</head>
<body>
  <section class="card">
    <div class="decor decor--flower-large" role="img" aria-label="Faint pale green flower illustration"></div>
    <div class="decor decor--flower-mid" role="img" aria-label="Faint green flower bud illustration"></div>
    <div class="decor decor--flower-small" role="img" aria-label="Faint green flower bud illustration"></div>
    <div class="decor decor--butterfly" role="img" aria-label="Faint pale green butterfly illustration"></div>

    <h1 class="brand-title">Petals On Harwood</h1>
    <p class="proprietors">Dana &amp; Lee Morcombe</p>

    <div class="rule"></div>

    <div class="contact-band">
      <address class="address">
        Petals on Harwood<br>
        42 Harwood street<br>
        Kellbrook Downs 3917
      </address>
      <ul class="contact-list">
        <li>
          <svg viewBox="0 0 24 24" aria-label="Phone"><path d="M6.6 2.5l3 3.2-1.8 2.4c1.2 2.6 3.4 4.9 6.1 6.1l2.4-1.8 3.2 3-2 3.1C10 18.3 5.7 14 3.5 6.5z"/><path d="M14 3a7 7 0 0 1 7 7h-1.6A5.4 5.4 0 0 0 14 4.6zM14 6.2a3.8 3.8 0 0 1 3.8 3.8h-1.6A2.2 2.2 0 0 0 14 7.8z"/></svg>
          0351938264
        </li>
        <li>
          <svg viewBox="0 0 24 24" aria-label="Fax"><path d="M7 1h10v8H7zM9 3v1h6V3zm0 2.5v1h6v-1z"/><path d="M3 11h18v11H3zm3 3v2h3v-2zm5 0v2h3v-2zm5 0v2h3v-2z"/></svg>
          0351938207
        </li>
        <li>
          <svg viewBox="0 0 24 24" aria-label="Email"><path d="M2 10l10-7 10 7v11H2zm2 1.2V19h16v-7.8l-8 5.3z"/></svg>
          poh@wattlemail.net.au
        </li>
      </ul>
    </div>
  </section>
</body>
</html>
```